redesign of my existing custom website into Wordpress based website

I need someone to redesign my current website into something more classy, simplistic, modern and on trend. I would like it set up on Wordpress in a way thats easy for me to make my own additions to blogs/price changes and promotion banners. I will also need a page that is password protected so members can login and have access to all my training videos and resources.
website is www.tidewellmamas.com.au

Target Market(s)

new mums

Industry/Entity Type

Fitness

Coding

Coded - Design and coding required

Number of Pages Required

5+ page

Colors
33a6d7

Requirements
Must have
• chic, modern, stylish and simplistic.
• a call to action above the page fold
• mobile friendly conversion
• a pop up message as soon as someone enters my sight offering my free report
• a members page that is password protected containing 3 youtube videos and 6 pdf attachments as resources
• a home page
• a contact us page
• an about us page
• a blog page
• a store page
Nice to have
• some examples of my peers websites that I like:
• www.norapellwick.com
• https://www.9qlr.com
• https://41bytedgarth.com
Should not have
• anything gimmicky

```html
<!DOCTYPE html>
<html lang="en">
<head>
<meta charset="utf-8">
<title>Tidewell Mamas – Home Fitness</title>
<link rel="stylesheet" href="https://fonts.googleapis.com/css2?family=Jost:wght@300;400;500&family=Open+Sans:wght@400;600&display=swap">
<style>
:root{
  --blue:#33a6d7;
  --blue-deep:#1d7fa8;
  --pink:#c2185b;
  --ink:#2b2b2b;
  --muted:#6a6a6a;
  --paper:#f4f4f4;
  --dark:#1b1b1b;
  --line:#d6d6d6;
}
*{box-sizing:border-box;margin:0;padding:0}
html,body{width:1200px;height:2932px;overflow:hidden}
body{position:relative;background:var(--paper);font-family:"Open Sans",Arial,sans-serif;color:var(--ink)}
.abs{position:absolute}
.head{font-family:"Jost",Helvetica,sans-serif;font-weight:400;letter-spacing:.5px}

/* header + hero */
.hero{left:0;top:0;width:1200px;height:622px;background:linear-gradient(100deg,#f3f2f0 0%,#ecebe8 40%,#e2ddd6 60%,#d9cfc3 100%)}
.hero-photo{left:520px;top:0;width:680px;height:622px;background:
  radial-gradient(ellipse 120px 170px at 92% 12%,rgba(116,158,84,.75),rgba(116,158,84,0) 100%),
  radial-gradient(ellipse 150px 120px at 70% 18%,rgba(214,170,140,.9),rgba(214,170,140,0) 100%),
  radial-gradient(ellipse 230px 240px at 72% 55%,rgba(198,186,168,.95),rgba(198,186,168,0) 100%),
  radial-gradient(ellipse 260px 90px at 62% 92%,rgba(126,104,96,.75),rgba(126,104,96,0) 100%),
  radial-gradient(ellipse 200px 180px at 22% 55%,rgba(238,228,232,.9),rgba(238,228,232,0) 100%),
  linear-gradient(100deg,rgba(236,234,231,0),#d6cbbd 70%,#c9bba9)}
.logo{left:98px;top:12px;width:138px;height:138px;border-radius:50%;background:#fff;border:3px solid #e8e8e8;display:flex;flex-direction:column;align-items:center;justify-content:center;text-align:center}
.logo span{font-family:"Jost",sans-serif;font-size:17px;color:var(--pink);line-height:1.15}
.nav{left:378px;top:30px;display:flex;gap:8px;align-items:center}
.nav a{font-family:"Jost",sans-serif;font-size:16px;color:#333;text-decoration:none;padding:8px 16px;border-radius:20px}
.nav a.on{border:2px solid var(--pink);color:var(--pink)}
.nav a.cart{background:var(--blue);color:#fff;margin-left:6px;padding:8px 22px}
.hero-copy{left:88px;top:242px}
.hero-copy .lead{font-size:20px;color:#333}
.hero-copy .kicker{font-family:"Jost",sans-serif;font-size:22px;color:var(--pink);margin-top:10px}
.hero-copy ul{list-style:none;margin-top:14px}
.hero-copy li{font-size:17px;color:#333;line-height:30px;padding-left:26px;position:relative}
.hero-copy li svg{position:absolute;left:0;top:8px}
.btn-blue{display:inline-block;margin-top:22px;background:var(--blue);color:#fff;font-size:14px;padding:12px 24px;border-radius:22px}
.dots{left:90px;top:504px;display:flex;gap:8px}
.dots span{width:28px;height:28px;border-radius:50%;background:#555}

/* welcome */
.welcome-title{left:0;top:676px;width:1200px;text-align:center;font-size:36px;color:var(--blue-deep)}
.welcome-text{left:130px;top:744px;width:940px;text-align:center;font-size:13.5px;line-height:22px;color:#444}
.feature{top:825px;width:300px;text-align:center}
.feature .ph{width:176px;height:176px;border-radius:50%;margin:0 auto}
.ph-workout{background:radial-gradient(circle at 45% 35%,#d7a08f 0%,#a8636a 30%,#6e3446 60%,#2e2228 100%)}
.ph-trainer{background:radial-gradient(ellipse 70px 55px at 50% 85%,#a6d36b 0%,#8cbf55 60%,rgba(140,191,85,0) 100%),radial-gradient(circle at 50% 38%,#e3c29f 0%,#c9a27a 35%,#8d7358 70%,#4e4034 100%)}
.ph-recipes{background:radial-gradient(ellipse 60px 80px at 55% 65%,#9fd05a 0%,rgba(159,208,90,0) 100%),radial-gradient(circle at 50% 35%,#c58a7a 0%,#7a4456 40%,#3e2a3c 75%,#221a24 100%)}
.feature h3{font-family:"Jost",sans-serif;font-weight:400;font-size:22px;margin-top:28px;color:#222}
.feature p{font-size:13px;line-height:20px;color:#666;margin:14px auto 0;width:240px}
.feature a{display:block;margin-top:10px;font-size:13.5px;color:var(--pink);text-decoration:none}

/* blue band */
.band{left:0;top:1208px;width:1200px;height:322px;background:linear-gradient(135deg,#2c8fbd,#33a6d7 50%,#2a86b2)}
.band h2{position:absolute;top:48px;width:100%;text-align:center;color:#fff;font-size:34px}
.band h4{position:absolute;top:106px;width:100%;text-align:center;color:#fff;font-family:"Jost",sans-serif;font-weight:300;font-size:24px}
.band p{position:absolute;top:146px;width:100%;text-align:center;color:#e6f4fb;font-size:14px}
.field{background:#fff;border:1px solid #ddd;height:52px;font-size:13px;color:#777;padding:0 14px;display:flex;align-items:center}
.btn-pink{background:var(--pink);color:#fff;font-size:13px;font-weight:600;height:52px;display:flex;align-items:center;justify-content:center}

/* program */
.program-title{left:88px;top:1612px;font-size:25px;color:#222;white-space:nowrap}
.program-list{left:88px;top:1660px;list-style:none}
.program-list li{font-size:13px;line-height:21.5px;color:#333;padding-left:18px;position:relative}
.program-list li::before{content:"»";position:absolute;left:0;color:#333}
.btn-outline{left:88px;top:1832px;border:2px solid var(--pink);color:var(--pink);border-radius:18px;font-size:12px;padding:7px 16px}
.video{left:627px;top:1587px;width:479px;height:298px;border:6px solid #fff;box-shadow:0 0 0 1px #ccc;background:
  radial-gradient(ellipse 110px 70px at 62% 42%,rgba(214,120,160,.85),rgba(214,120,160,0) 100%),
  radial-gradient(ellipse 60px 70px at 24% 62%,rgba(224,196,178,.85),rgba(224,196,178,0) 100%),
  radial-gradient(ellipse 80px 110px at 90% 25%,rgba(196,138,96,.8),rgba(196,138,96,0) 100%),
  linear-gradient(180deg,#3c3836 0%,#2a2727 45%,#352c4a 72%,#4d3d86 100%)}
.play{left:828px;top:1697px}

/* testimonial */
.quote{left:0;top:1940px;width:1200px;height:274px;background:linear-gradient(90deg,#1a1a1a,#262626 60%,#151515)}
.avatar{left:132px;top:1992px;width:164px;height:164px;border-radius:50%;background:radial-gradient(circle at 50% 45%,#efd9c6 0%,#dcbc9e 35%,#c9a56e 65%,#8b7a6c 100%);border:4px solid #333}
.qmark{left:132px;top:1990px;width:44px;height:44px;border-radius:50%;background:var(--pink);color:#fff;font-family:Georgia,serif;font-size:34px;text-align:center;line-height:52px}
.quote-text{left:318px;top:2000px;width:770px;font-size:14.5px;line-height:24px;color:#bdbdbd}
.quote-by{left:322px;top:2116px;font-size:15px;line-height:24px;color:#aaa}

/* news */
.news-title{left:0;top:2262px;width:1200px;text-align:center;font-size:26px;color:#222}
.news{top:2324px;width:313px;text-align:center}
.news .ph{height:200px}
.ph-plank{background:radial-gradient(ellipse 90px 30px at 45% 62%,rgba(120,170,150,.8),rgba(120,170,150,0) 100%),linear-gradient(180deg,#b9a89a 0%,#8b7b70 35%,#2e2a2a 55%,#3f3a4e 78%,#5a4a8a 100%)}
.ph-baby{background:radial-gradient(ellipse 70px 40px at 38% 38%,rgba(222,92,140,.85),rgba(222,92,140,0) 100%),radial-gradient(ellipse 60px 50px at 68% 62%,rgba(150,170,200,.7),rgba(150,170,200,0) 100%),linear-gradient(180deg,#4a2a34 0%,#2e2626 45%,#55505a 75%,#7a7380 100%)}
.ph-weights{background:radial-gradient(ellipse 55px 80px at 50% 68%,rgba(168,222,70,.9),rgba(168,222,70,0) 100%),radial-gradient(ellipse 45px 45px at 50% 28%,rgba(224,192,160,.9),rgba(224,192,160,0) 100%),linear-gradient(180deg,#3a2630 0%,#2a2426 50%,#3c3a40 100%)}
.news h5{font-family:"Open Sans",sans-serif;font-weight:400;font-size:15px;color:#222;margin-top:20px}
.news small{display:block;font-size:12px;color:#666;margin-top:4px}

/* footer */
.footer{left:0;top:2652px;width:1200px;height:280px;background:#ececec;border-top:1px solid var(--line)}
.f-logo{left:90px;top:2712px;width:150px;text-align:center}
.f-logo .mark{width:58px;height:58px;border-radius:50%;background:var(--pink);margin:0 auto 10px}
.f-logo span{font-family:"Jost",sans-serif;font-size:18px;color:var(--pink)}
.f-col h6{font-family:"Jost",sans-serif;font-weight:400;font-size:15px;color:#333;letter-spacing:.5px}
.f-col p{font-size:10.5px;line-height:20px;color:#666;margin-top:16px}
.mail{display:flex;margin-top:8px}
.mail .in{width:150px;height:30px;background:#fff;border:1px solid #ccc;font-size:10.5px;color:#888;padding:0 8px;display:flex;align-items:center}
.mail .go{width:56px;height:30px;background:var(--pink);color:#fff;font-size:11px;display:flex;align-items:center;justify-content:center}
.social{display:flex;gap:14px;margin-top:26px}
.social span{width:24px;height:24px;background:#555;border-radius:3px}
.rule{left:88px;top:2856px;width:1024px;height:1px;background:var(--line)}
.copy{left:0;top:2886px;width:1200px;text-align:center;font-size:11px;color:#555}

/* popup */
.shade{left:0;top:0;width:1200px;height:2932px;background:rgba(30,30,30,.42)}
.popup{left:199px;top:215px;width:777px;height:381px;background:#fff;border-radius:4px;box-shadow:0 4px 30px rgba(0,0,0,.35)}
.popup .close{position:absolute;right:18px;top:12px;font-size:30px;color:#444;line-height:1}
.popup h2{position:absolute;top:52px;width:100%;text-align:center;font-size:31px;color:var(--blue)}
.popup h3{position:absolute;top:110px;width:100%;text-align:center;font-family:"Jost",sans-serif;font-weight:400;font-size:22px;color:#222}
.popup p{position:absolute;top:152px;width:100%;text-align:center;font-size:13px;color:#555}
.popup .field{position:absolute;top:196px;width:276px;height:50px;border-radius:6px;border-color:#ccc;background:#fafafa;font-size:12px;color:#444}
.popup .cta{position:absolute;left:293px;top:275px;width:192px;height:44px;border-radius:22px;background:var(--blue);color:#fff;font-size:15px;font-weight:600;display:flex;align-items:center;justify-content:center}
</style>
</head>
<body>

<header>
  <div class="abs hero"></div>
  <div class="abs hero-photo" role="img" aria-label="Photo of a smiling mother exercising at home with her baby"></div>
  <div class="abs logo"><span>Tidewell<br>Mamas</span></div>
  <nav class="abs nav">
    <a class="on">HOME</a><a>ABOUT US</a><a>PROGRAM</a><a>BLOG</a><a>SHOP</a><a>CONTACT US</a><a class="cart">My cart</a>
  </nav>
  <div class="abs hero-copy">
    <div class="lead">Lose your baby weight with our</div>
    <div class="kicker">12 WEEK HOME FITNESS PROGRAM</div>
    <ul>
      <li><svg width="16" height="14"><path d="M1 7l5 5 9-11" stroke="#c2185b" stroke-width="3" fill="none"/></svg>12 week, catch-up friendly plan</li>
      <li><svg width="16" height="14"><path d="M1 7l5 5 9-11" stroke="#c2185b" stroke-width="3" fill="none"/></svg>Workout equipment included</li>
      <li><svg width="16" height="14"><path d="M1 7l5 5 9-11" stroke="#c2185b" stroke-width="3" fill="none"/></svg>Accountability and support</li>
      <li><svg width="16" height="14"><path d="M1 7l5 5 9-11" stroke="#c2185b" stroke-width="3" fill="none"/></svg>Family friendly recipes</li>
    </ul>
    <span class="btn-blue">GET STARTED</span>
  </div>
  <div class="abs dots"><span></span><span></span></div>
</header>

<section>
  <h1 class="abs head welcome-title">WELCOME TO TIDEWELL MAMAS</h1>
  <p class="abs welcome-text">After a life time of competitive sports and as a qualified personal trainer, I thought I knew exactly what it would take to get my body back after having babies. I put on a massive 30 kgs with my first pregnancy and found myself in a situation for the first time in my life where I had to lose a lot of weight.</p>
  <div class="abs feature" style="left:108px"><div class="ph ph-workout" role="img" aria-label="Photo of a mum doing a workout"></div><h3>WORKOUT PROGRAM</h3><p>This sparked a huge determination and curiosity within me and I spent the next 2 years studying and researching</p><a>Read More →</a></div>
  <div class="abs feature" style="left:452px"><div class="ph ph-trainer" role="img" aria-label="Photo of the trainer"></div><h3>TRAINING PROGRAM</h3><p>This sparked a huge determination and curiosity within me and I spent the next 2 years studying and researching</p><a>Read More →</a></div>
  <div class="abs feature" style="left:794px"><div class="ph ph-recipes" role="img" aria-label="Photo of a mum training with weights"></div><h3>HEALTHY RECIPES</h3><p>This sparked a huge determination and curiosity within me and I spent the next 2 years studying and researching</p><a>Read More →</a></div>
</section>

<section class="abs band">
  <h2 class="head">GET YOUR FREE TOP 10</h2>
  <h4>Baby Belly Blasting Tips</h4>
  <p>See our secret tips to a flatter yummy mummy tummy that you can start implementing</p>
  <div class="abs field" style="left:217px;top:199px;width:291px">NAME</div>
  <div class="abs field" style="left:525px;top:199px;width:236px">EMAIL ID</div>
  <div class="abs btn-pink" style="left:825px;top:199px;width:158px">GET IT FREE NOW!</div>
</section>

<section>
  <h2 class="abs head program-title">WHAT'S INCLUDED IN THE PROGRAM?</h2>
  <ul class="abs program-list">
    <li>Our unique 3 stage, 12 week training program</li>
    <li>Full instructional Workout DVD and program cards for each program</li>
    <li>Weekly accountability charts</li>
    <li>Weekly coaching emails</li>
    <li>Funky exercise equipment for your home</li>
    <li>Nutritionist approved healthy eating guide</li>
    <li>Healthy Family Favourites recipe ebook</li>
  </ul>
  <span class="abs btn-outline">READ MORE »</span>
  <div class="abs video" role="img" aria-label="Video still of a mum exercising on the living room floor beside her baby"></div>
  <svg class="abs play" width="66" height="66"><circle cx="33" cy="33" r="32" fill="rgba(0,0,0,.55)"/><path d="M26 20l20 13-20 13z" fill="#fff"/></svg>
</section>

<section>
  <div class="abs quote"></div>
  <div class="abs avatar" role="img" aria-label="Portrait photo of the founder"></div>
  <div class="abs qmark">“</div>
  <p class="abs quote-text">It has survived not only five centuries, but also the leap into electronic typesetting, remaining essentially unchanged. It was popularised in the 1960s with the release of Lettervane sheets containing Lorem Ipsum passages, and more recently with desktop publishing software like Orvel PageSmith including versions of Lorem Ipsum t has survived not only five centuries, but also the leap into electronic typesetting.</p>
  <p class="abs quote-by">Porro quisquam<br>Founder, dolorem ipsum</p>
</section>

<section>
  <h2 class="abs head news-title">LATEST NEWS</h2>
  <article class="abs news" style="left:92px"><div class="ph ph-plank" role="img" aria-label="Photo of a side plank workout"></div><h5>Neque porro quisquam est qui</h5><small>19/05/17</small></article>
  <article class="abs news" style="left:446px"><div class="ph ph-baby" role="img" aria-label="Photo of a mum exercising with her baby"></div><h5>Dolorem ipsum quia dolor sit amet</h5><small>17/05/17</small></article>
  <article class="abs news" style="left:796px"><div class="ph ph-weights" role="img" aria-label="Photo of the trainer with hand weights"></div><h5>Quisquam est qui dolorem</h5><small>13/05/17</small></article>
</section>

<footer>
  <div class="abs footer"></div>
  <div class="abs f-logo"><div class="mark"></div><span>Tidewell Mamas</span></div>
  <div class="abs f-col" style="left:332px;top:2694px;width:220px">
    <h6>CONTACT US</h6>
    <p>Address : 14 Harbourline Rd, Eastmere<br>Sydney NSW 2000<br>Phone : (02) 5550 1847<br>Email : hello@tidewellmamas.com.au</p>
  </div>
  <div class="abs f-col" style="left:617px;top:2694px;width:240px">
    <h6>JOIN OUR MAILING LIST</h6>
    <p style="margin-top:10px;line-height:16px">Your email is safe with us, we never share it.</p>
    <div class="mail"><div class="in">Email address</div><div class="go">Submit</div></div>
  </div>
  <div class="abs f-col" style="left:935px;top:2694px">
    <h6>FOLLOW US OUT THERE</h6>
    <div class="social"><span></span><span></span><span></span><span></span></div>
  </div>
  <div class="abs rule"></div>
  <p class="abs copy">Copyright © 2017. All Rights Reserved</p>
</footer>

<div class="abs shade"></div>
<aside class="abs popup">
  <span class="close">×</span>
  <h2 class="head">GET YOUR FREE TOP 10</h2>
  <h3>BABY BELLY BLASTING TIPS</h3>
  <p>See our secret tips to a flatter yummy mummy tummy that you can start implementing</p>
  <div class="field" style="left:104px">Name</div>
  <div class="field" style="left:399px">Email</div>
  <div class="cta">GET IT FREE NOW!</div>
</aside>

</body>
</html>
```